Federal IT Consulting Company - Brisolux Consulting Group

We're seeking a skilled web designer to create a modern, bold, and engaging WordPress website for Brisolux Consulting Group, LLC. Our company specializes in federal IT consulting, and our name is a play on "Brightening Solutions." The website should reflect our expertise in the federal technology marketplace and position us as a trusted partner for clients navigating their IT journey.

contact: info@brisoluxgrp-example.com

Current Status

WordPress is already installed on our hosting account
We have an existing logo (may need modernization)

Design Requirements

Style:

Modern and visually striking design
Bold elements to convey confidence and expertise
Incorporate the concept of "brightening solutions" into the design

Features:

Modern UX sliders for dynamic content presentation
Eye-catching, high-quality images (stock photos to be sourced by the designer)
Responsive design for all devices

Color Scheme:

To be proposed by the designer, should align with our brand and convey trust and technological expertise

Logo:

Evaluate our current logo
Create a transparent background version if needed
Propose modernization if deemed necessary

Accessibility:

Ensure design elements are accessible to users with disabilities
Use high contrast ratios for text and background colors
Provide text alternatives for non-text content

Website Structure
Create the following pages, with the possibility of subpages:

Home
Services
About
Contact

Specific Page Requirements
Home Page

Striking hero section with a clear value proposition
Overview of our services
Client testimonials or trust indicators

Services Page

Detailed list of our IT consulting services
Clear explanation of how we help navigate the federal IT landscape

About Page

Company history and mission
Team highlights (if applicable)
Our approach to federal IT consulting

Contact Page

Contact form
Other contact methods (phone, email)

Technical Requirements

Fully responsive design
SEO best practices implemented
Fast loading times
Integration with necessary plugins (to be discussed)
Training on how to update and maintain the site
Full compliance with Web Content Accessibility Guidelines (WCAG) 2.1 Level AA
Adherence to Section 508 standards for federal website accessibility
Implementation of necessary features for ADA compliance
Updates

Designs look the same

Target Market(s)

US Federal Govt customers looking for IT support.

Industry/Entity Type

IT Consulting

Coding

Coded - Design and coding required

Colors
0054AA
0677BA
7BADD7
CADEEF
E8F1F8
0094D4
00A9DD
6FCCEA
C7EBF8
E9F6FB
00AB8E
00BBA5
67D7C9
C6EFE9
E9F9F6

```html
<!DOCTYPE html>
<html lang="en">
<head>
<meta charset="utf-8">
<title>Brisolux Federal Services</title>
<link rel="stylesheet" href="https://fonts.googleapis.com/css2?family=Montserrat:wght@400;500;600&display=swap">
<style>
:root{
  --navy:#0b3a5c;
  --blue:#0094d4;
  --cyan:#00a9dd;
  --deep:#0677ba;
  --pale:#e9f6fb;
  --ice:#c7ebf8;
  --text:#2f3d4a;
  --white:#ffffff;
}
*{box-sizing:border-box;margin:0;padding:0}
html,body{width:1200px;height:2945px;overflow:hidden}
body{font-family:"Montserrat",sans-serif;color:var(--text);background:var(--white);position:relative}
a{color:inherit;text-decoration:none}
.abs{position:absolute}
.btn{display:inline-flex;align-items:center;justify-content:center;background:var(--cyan);color:var(--white);border-radius:20px;font-size:15px;font-weight:500}
.eyebrow{color:var(--blue);font-size:20px;font-weight:500;display:flex;align-items:center;gap:14px}
.eyebrow::before{content:"";width:34px;height:1.5px;background:var(--blue)}
.h2{font-size:37px;font-weight:500;color:var(--navy);line-height:1.25}
.h2 em{font-style:normal;color:var(--blue)}
.body{font-size:14px;line-height:26px;color:var(--text)}

/* hero */
.hero{left:0;top:0;width:1200px;height:557px;background:var(--pale);overflow:hidden}
.hero-ring{left:580px;top:100px;width:580px;height:580px;border-radius:50%;border:70px solid #d3eef8}
.brand{display:flex;align-items:center;gap:10px;font-size:32px;font-weight:600;color:var(--navy);letter-spacing:1px}
.brand-dot{width:34px;height:34px;border-radius:50%;background:var(--blue)}
.nav{left:535px;top:44px;display:flex;gap:25px;font-size:15px;color:#4a5560}
.nav .active{color:var(--blue);font-weight:500}
.hero-photo{left:585px;top:155px;width:590px;height:405px;background:linear-gradient(135deg,#d8e4ec,#8fa3b1 55%,#4d5660);border-radius:4px 4px 0 0}
.hero h1{font-size:45px;font-weight:500;color:var(--navy);line-height:50px}

/* about */
.about-photo{left:111px;top:644px;width:445px;height:472px;border-radius:12px;background:linear-gradient(160deg,#c9b08f,#7a6a5a 50%,#3b3d44)}
.feature h3{font-size:23px;font-weight:500;color:var(--navy)}
.feature p{font-size:14px;line-height:23px;margin-top:10px}

/* services */
.services{left:0;top:1204px;width:1200px;height:621px;background:var(--pale);overflow:hidden}
.card{width:300px;height:277px;border:1.5px solid #5cc2e8;border-radius:8px;background:var(--pale);padding:28px 25px}
.card h3{font-size:22px;font-weight:500;color:var(--navy);margin-top:22px}
.card p{font-size:14px;line-height:22px;margin-top:14px}
.more{font-size:15px;font-weight:500;color:var(--navy);text-decoration:underline;display:inline-block;margin-top:14px}

/* testimonials */
.quote{width:292px;height:185px;border-radius:12px;background:var(--white);box-shadow:0 3px 10px rgba(0,0,0,.18);padding:20px 17px;overflow:hidden}
.quote p{font-size:14px;line-height:22px;text-align:justify}
.quote .rule{width:54px;height:2px;background:var(--blue);margin-top:23px}
.quote .who{display:flex;justify-content:space-between;align-items:center;margin-top:6px}
.quote .who b{font-size:19px;font-weight:600;color:var(--navy)}
.stars{color:#f7a21b;font-size:15px;letter-spacing:1px}

/* cta + footer */
.lower{left:0;top:2365px;width:1200px;height:580px;background:var(--pale)}
.cta{left:111px;top:2448px;width:978px;height:169px;background:linear-gradient(100deg,#0677ba,#0094d4 60%,#00bde6);display:flex;align-items:center;justify-content:space-between;padding:0 45px}
.cta h2{font-size:37px;font-weight:500;color:var(--white);line-height:46px}
.cta h2 em{font-style:normal;color:var(--navy)}
.cta .btn{background:var(--white);color:var(--blue);width:145px;height:40px}
.col h4{font-size:19px;font-weight:600;color:var(--navy);margin-bottom:18px}
.col li{list-style:none;font-size:14px;line-height:26px;color:var(--text)}
.col li::before{content:"» ";color:var(--blue)}
.contact li::before{content:none}
.contact li{display:flex;gap:14px;margin-bottom:8px;line-height:22px}
.legal{left:109px;top:2897px;width:980px;display:flex;justify-content:space-between;font-size:14px}
.legal em{font-style:normal;color:var(--blue)}
</style>
</head>
<body>

<section class="hero abs">
  <div class="hero-ring abs"></div>
  <a class="brand abs" style="left:111px;top:36px"><span class="brand-dot"></span>BRISOLUX</a>
  <nav class="nav abs"><a class="active">Home</a><a>Services</a><a>About</a><a>Contact</a></nav>
  <a class="btn abs" style="left:945px;top:34px;width:144px;height:38px">Get Started</a>
  <p class="abs" style="left:110px;top:163px;font-size:20px;font-weight:500;color:var(--blue)">Nemo Enim Ipsam Voluptatem</p>
  <h1 class="abs" style="left:111px;top:198px;width:480px">Empowering Federal Agencies through IT Excellence</h1>
  <p class="body abs" style="left:111px;top:361px;width:450px">Lorem ipsum dolor sit amet, consectetur adipiscing elit, sed do eiusmod tempor incididunt</p>
  <a class="btn abs" style="left:111px;top:433px;width:145px;height:40px">Contact Us</a>
  <div class="hero-photo abs" role="img" aria-label="Three colleagues at office desks celebrating with a high five"></div>
</section>

<section>
  <div class="about-photo abs" role="img" aria-label="Consultants discussing work around a laptop"></div>
  <p class="eyebrow abs" style="left:600px;top:652px">About Us</p>
  <h2 class="h2 abs" style="left:600px;top:695px;width:460px">Discover <em>Our Federal</em> IT Consulting Expertise</h2>
  <p class="body abs" style="left:600px;top:805px;width:490px">Lorem ipsum dolor sit amet, consectetur adipiscing elit, sed do eiusmod tempor incididunt ut labore et dolore magna aliqua. Quis ipsum suspendisse ultrices gravida risus commodo viverra maecenas accumsan lacus vel facilisis.</p>
  <div class="feature abs" style="left:600px;top:932px;display:flex;gap:16px">
    <svg width="52" height="52" viewBox="0 0 52 52" fill="none" stroke="#0094d4" stroke-width="2"><circle cx="24" cy="28" r="20"/><circle cx="24" cy="28" r="12"/><circle cx="24" cy="28" r="4"/><path d="M24 28L44 8M38 8h6v6"/></svg>
    <div><h3>Mission</h3><p>Lorem ipsum dolor sit<br>amet, consectetur</p></div>
  </div>
  <div class="feature abs" style="left:857px;top:932px;display:flex;gap:16px">
    <svg width="52" height="52" viewBox="0 0 52 52" fill="none" stroke="#0094d4" stroke-width="2"><circle cx="32" cy="16" r="8"/><path d="M29 26h6M32 2v3M44 16h3M17 16h3M4 34h8v14H4zM12 38h12l12-4c4 0 4 4 0 6l-12 6H12"/></svg>
    <div><h3>Vision</h3><p>Lorem ipsum dolor sit<br>amet, consectetur</p></div>
  </div>
  <a class="btn abs" style="left:600px;top:1044px;width:145px;height:39px">Learn More →</a>
</section>

<section class="services abs">
  <p class="eyebrow abs" style="left:111px;top:80px">Services</p>
  <h2 class="h2 abs" style="left:111px;top:122px">Strategic IT Consulting<br>for <em>Federal</em> Agencies</h2>
  <a class="abs" style="left:940px;top:190px;font-size:15px;font-weight:500;color:var(--navy);text-decoration:underline">View All Services →</a>
  <article class="card abs" style="left:111px;top:259px">
    <svg width="60" height="56" viewBox="0 0 60 56" fill="none" stroke="#0094d4" stroke-width="2"><rect x="2" y="4" width="46" height="34"/><path d="M10 32v-8M18 32v-14M26 32v-10M10 18l10-8 8 6 10-8"/><circle cx="46" cy="38" r="8"/><path d="M52 44l6 6M16 38l-4 14M34 38l4 14"/></svg>
    <h3>Sed Ut Perspiciatis</h3>
    <p>Lorem ipsum dolor sit amet, consectetur adipiscing elit, sed do eiusmod tempor incididunt</p>
    <a class="more">Read More →</a>
  </article>
  <article class="card abs" style="left:450px;top:259px">
    <svg width="60" height="56" viewBox="0 0 60 56" fill="none" stroke="#0094d4" stroke-width="2"><path d="M24 2l22 8v16c0 14-10 24-22 28C12 50 2 40 2 26V10z"/><path d="M24 8l16 6v12c0 10-7 18-16 21C15 44 8 36 8 26V14z"/><rect x="17" y="24" width="14" height="11"/><path d="M20 24v-4a4 4 0 018 0v4"/></svg>
    <h3>Sed Ut Perspiciatis</h3>
    <p>Lorem ipsum dolor sit amet, consectetur adipiscing elit, sed do eiusmod tempor incididunt</p>
    <a class="more">Read More →</a>
  </article>
  <article class="card abs" style="left:789px;top:259px">
    <svg width="60" height="56" viewBox="0 0 60 56" fill="none" stroke="#0094d4" stroke-width="2"><path d="M12 28a8 8 0 010-16 12 12 0 0124-2 8 8 0 0110 18z"/><path d="M16 28v16M24 28v22M32 28v16M40 28v10"/><circle cx="16" cy="46" r="2"/><circle cx="24" cy="52" r="2"/><circle cx="32" cy="46" r="2"/><circle cx="40" cy="40" r="2"/></svg>
    <h3>Sed Ut Perspiciatis</h3>
    <p>Lorem ipsum dolor sit amet, consectetur adipiscing elit, sed do eiusmod tempor incididunt</p>
    <a class="more">Read More →</a>
  </article>
</section>

<section>
  <p class="eyebrow abs" style="left:510px;top:1906px">Testimonials</p>
  <h2 class="h2 abs" style="left:0;top:1951px;width:1200px;text-align:center">What <em>Our Customers</em><br>Say About Us</h2>
  <article class="quote abs" style="left:-50px;top:2092px">
    <p>Lorem ipsum dolor sit amet, consectetur adipiscing elit, sed do eiusmod tempor incididunt ut labore et dolore magna aliqua</p>
    <div class="rule"></div><div class="who"><b>Alexander</b><span class="stars">★★★★☆</span></div>
  </article>
  <article class="quote abs" style="left:287px;top:2092px">
    <p>Lorem ipsum dolor sit amet, consectetur adipiscing elit, sed do eiusmod tempor incididunt ut labore et dolore magna aliqua</p>
    <div class="rule"></div><div class="who"><b>Alexander</b><span class="stars">★★★★☆</span></div>
  </article>
  <article class="quote abs" style="left:621px;top:2092px">
    <p>Lorem ipsum dolor sit amet, consectetur adipiscing elit, sed do eiusmod tempor incididunt ut labore et dolore magna aliqua</p>
    <div class="rule"></div><div class="who"><b>Alexander</b><span class="stars">★★★★☆</span></div>
  </article>
  <article class="quote abs" style="left:956px;top:2092px">
    <p>Lorem ipsum dolor sit amet, consectetur adipiscing elit, sed do eiusmod tempor incididunt ut labore et dolore magna aliqua</p>
    <div class="rule"></div><div class="who"><b>Alexander</b><span class="stars">★★★★☆</span></div>
  </article>
</section>

<footer class="lower abs">
</footer>
<div class="cta abs">
  <h2>Reach <em>Our Federal</em> IT Consulting<br>Specialists</h2>
  <a class="btn">Contact Us</a>
</div>
<div class="abs" style="left:111px;top:2672px;width:290px">
  <a class="brand" style="font-size:28px"><span class="brand-dot" style="width:30px;height:30px"></span>BRISOLUX</a>
  <p class="body" style="margin-top:22px">Lorem ipsum dolor sit amet, consectetur adipiscing elit, sed do eiusmod tempor incididunt ut labore et dolore magna aliqua.</p>
</div>
<div class="col abs" style="left:458px;top:2696px"><h4>Quick Links</h4><ul><li>Home</li><li>About Us</li><li>Services</li><li>Contact Us</li></ul></div>
<div class="col abs" style="left:646px;top:2696px"><h4>Other Links</h4><ul><li>Company overview</li><li>Careers</li><li>Partners</li><li>Our team</li></ul></div>
<div class="col contact abs" style="left:882px;top:2696px;width:210px"><h4>Contact Info</h4><ul>
  <li><svg width="14" height="18" viewBox="0 0 14 18"><path d="M7 0a7 7 0 00-7 7c0 5 7 11 7 11s7-6 7-11a7 7 0 00-7-7z" fill="#0094d4"/><circle cx="7" cy="7" r="2.5" fill="#fff"/></svg><span>1254, Sed ut perspiciatis unde omnis</span></li>
  <li><svg width="16" height="16" viewBox="0 0 16 16"><path d="M3 1l3 3-2 2c1 3 3 5 6 6l2-2 3 3-2 2C7 15 1 9 1 3z" fill="#0094d4"/></svg><span>+1 888 8888 8888</span></li>
  <li><svg width="16" height="14" viewBox="0 0 16 14"><rect y="1" width="16" height="12" fill="#0094d4"/><path d="M0 2l8 6 8-6" stroke="#fff" stroke-width="1.5" fill="none"/></svg><span>info@brisolux-example.com</span></li>
</ul></div>
<div class="legal abs">
  <span>Copyright 2024 <em>Brisolux Federal Services, LLC.</em>. All Rights Reserved.</span>
  <span>Terms &amp; Conditions &nbsp;| &nbsp;Privacy Policy &nbsp;| &nbsp;Sitemaps</span>
</div>

</body>
</html>
```